Kestrelford Therapy and Consulting

Build & publish a WordPress website that advertises and markets my private practice - which is delivering, and consulting in, psychological therapies. I also need to be able to edit content (eg text and images) on the end product thereafter. It should have a call to action on the homepage, links to:
• About me
• For referrers (with link to service fees)
• Contact details – phone#, email address, location, operating hours, and service fees
• Other resources

Target Market(s)

People struggling with mental health, relationships, and/or psychological disorders

Industry/Entity Type

Mental health

Coding

Coded - Design and coding required

Number of Pages Required

4 page

Requirements
Must have
• WordPress
Nice to have
• Please make my logo standout on the home page
Should not have
• No testimonials - they're forbidden for psychologists in Australia

```html
<!DOCTYPE html>
<html lang="en">
<head>
<meta charset="utf-8">
<title>Kestrelford Therapy and Consulting</title>
<link rel="stylesheet" href="https://fonts.googleapis.com/css2?family=Cinzel:wght@400;500&family=Karla:wght@400;500;600&family=Lora:wght@400&display=swap">
<style>
:root{
  --teal:#33c3df;
  --purple:#c485da;
  --grad:linear-gradient(90deg,#36c5e0,#c98adb);
  --ink:#222;
  --text:#4a4a4a;
  --grey:#f2f2f2;
  --footer:#0c0c0c;
  --white:#fff;
}
*{box-sizing:border-box;margin:0;padding:0}
html,body{width:1200px;height:4839px;overflow:hidden}
body{font-family:"Karla",sans-serif;color:var(--text);background:var(--white);position:relative}
section,header,footer,.topbar{position:relative;width:1200px}
.abs{position:absolute}
.heading{font-family:"Cinzel",serif;color:var(--ink);font-weight:400;letter-spacing:1px}
.btn{position:absolute;display:inline-flex;align-items:center;justify-content:center;height:50px;border-radius:25px;background:var(--grad);color:#fff;font-family:"Cinzel",serif;font-size:14px;letter-spacing:1px;padding:0 26px}
.photo{position:absolute}

.topbar{height:47px;background:var(--teal);color:#fff;font-size:13px;display:flex;align-items:center;justify-content:center;font-weight:500}
.site-header{height:92px;background:#fff}
.brand{position:absolute;left:115px;top:24px;display:flex;align-items:center;gap:12px}
.brand-mark{width:42px;height:42px;border-radius:50%;border:3px solid var(--teal)}
.brand-name{font-family:"Cinzel",serif;font-size:28px;color:#3a3a3a}
.nav{position:absolute;left:466px;top:36px;display:flex;gap:32px;font-size:15px;color:#333}
.site-header .btn{left:858px;top:20px;width:231px;height:52px}

.hero{height:687px;overflow:hidden}
.hero .photo{inset:0;background:linear-gradient(100deg,#e4e6e8 0%,#d6d8d9 40%,#c3c8cf 60%,#9aa6b6 80%,#d8d4cf 100%)}
.hero-text{position:absolute;left:113px;top:200px}
.hero-text .pre{font-family:"Cinzel",serif;font-size:32px;color:#222;letter-spacing:2px}
.hero-text h1{font-family:"Cinzel",serif;font-size:66px;font-weight:500;color:#222;letter-spacing:2px;margin-top:10px;line-height:1}
.hero-text .sub{font-size:25px;color:#333;margin-top:16px}
.hero .btn{left:113px;top:400px;width:156px}
.hero svg.curve{position:absolute;left:0;bottom:0}
.dots{position:absolute;left:574px;top:640px;display:flex;gap:8px}
.dots i{width:12px;height:12px;border-radius:50%;border:2px solid #fff;display:block}
.dots i.on{background:var(--teal);border-color:var(--teal)}

.about{height:671px}
.about .photo{left:117px;top:113px;width:452px;height:452px;border-radius:50%;border:8px solid var(--teal);background:radial-gradient(circle at 50% 55%,#a89a8e 0%,#6f7a5e 45%,#2e4a2c 100%)}
.about-body{position:absolute;left:652px;top:93px;width:436px}
.about-body h2{font-size:38px}
.about-body .name{font-size:29px;color:var(--teal);margin-top:14px;font-weight:500}
.about-body .role{font-size:20px;color:#222;margin-top:10px}
.about-body p{font-family:"Lora",serif;font-size:14px;line-height:26px;text-align:justify;margin-top:16px}
.about-body .qual-h{font-size:15px;margin-top:20px}
.about-body .qual{font-size:15px;margin-top:12px}
.about .btn{left:652px;top:526px;width:156px}

.services{height:541px;background:var(--grey)}
.services h2{position:absolute;top:74px;width:100%;text-align:center;font-size:38px}
.cards{position:absolute;left:113px;top:158px;display:flex}
.card{width:243px;height:214px;background:#f7f7f7;border:1px solid #e6e6e6;display:flex;flex-direction:column;align-items:center;justify-content:center;gap:22px;font-size:15px;color:#555}
.card.raised{background:#fff;box-shadow:0 2px 8px rgba(0,0,0,.08)}
.services .btn{left:530px;top:414px;width:140px}

.interests{height:488px}
.interests h2{position:absolute;top:78px;width:100%;text-align:center;font-size:38px}
.topic{position:absolute;top:165px;width:200px;text-align:center}
.topic .photo{position:relative;margin:0 auto;width:169px;height:169px;border-radius:50%}
.topic span{display:block;margin-top:28px;font-family:"Cinzel",serif;font-size:18px;color:#222;line-height:26px;letter-spacing:.5px}
.arrow{position:absolute;top:237px;width:30px;height:30px;border-radius:50%;border:1.5px solid var(--teal)}

.modalities{height:569px;background:var(--teal);overflow:hidden}
.modalities .photo{left:540px;top:0;width:660px;height:569px;background:linear-gradient(90deg,rgba(51,195,223,1) 0%,rgba(51,195,223,0) 18%),linear-gradient(120deg,#c9c3b9 0%,#8d7b6e 35%,#4f5660 60%,#b4aca4 85%,#2d3a4d 100%)}
.mod-text{position:absolute;left:118px;top:60px;width:462px;color:#fff}
.mod-text h2{font-size:38px;color:#fff}
.mod-text p{font-size:14.4px;line-height:25.8px;text-align:justify;margin-top:18px}
.outline-btn{position:absolute;left:118px;top:444px;width:150px;height:50px;border:2px solid #fff;border-radius:25px;color:#fff;font-family:"Cinzel",serif;font-size:14px;display:flex;align-items:center;justify-content:center;letter-spacing:1px}

.associations{height:567px}
.assoc-frame{position:absolute;left:101px;top:79px;width:427px;height:391px;border-radius:22px;background:var(--purple)}
.associations .photo{left:112px;top:90px;width:416px;height:380px;border-radius:16px;background:linear-gradient(110deg,#d9d4cc 0%,#c6a98f 35%,#e6e2dc 55%,#7f8a70 80%,#cfc8bd 100%)}
.assoc-body{position:absolute;left:601px;top:78px;width:500px}
.assoc-body h2{font-size:38px;line-height:52px}
.assoc-body ul{list-style:none;margin-top:18px}
.assoc-body li{position:relative;padding-left:38px;font-size:18.5px;color:#333;line-height:29px;margin-bottom:18px}
.assoc-body li svg{position:absolute;left:0;top:5px}
.associations .btn{left:600px;top:447px;width:150px}

.info-tabs{height:522px;background:var(--grey)}
.tab{position:absolute;top:62px;height:52px;border-radius:26px;border:2px solid var(--teal);color:var(--teal);font-family:"Cinzel",serif;font-size:14px;display:flex;align-items:center;justify-content:center;letter-spacing:.5px}
.tab.active{background:var(--teal);color:#fff}
.tab-body{position:absolute;left:113px;top:168px;width:460px}
.tab-body h2{font-size:38px}
.tab-body p{font-family:"Lora",serif;font-size:14.5px;line-height:26px;margin-top:28px}
.info-tabs .btn{left:113px;top:420px;width:150px}
.info-tabs .photo{left:637px;top:180px;width:477px;height:342px;background:linear-gradient(110deg,#d7c49e 0%,#b89468 35%,#6b4a3a 60%,#c9b08a 100%)}

.payment{height:291px}
.payment h2{position:absolute;top:78px;width:100%;text-align:center;font-size:38px}
.payment p{position:absolute;left:150px;top:148px;width:900px;text-align:center;font-family:"Lora",serif;font-size:14.5px;line-height:26px}

.site-footer{height:364px;background:var(--footer);color:#fff}
.site-footer .brand{left:117px;top:100px}
.site-footer .brand-name{color:#fff}
.social{position:absolute;left:117px;top:178px;display:flex;gap:22px}
.social i{width:18px;height:18px;border-radius:50%;background:#fff;display:block}
.f-col{position:absolute;top:80px}
.f-col h3{font-family:"Cinzel",serif;font-weight:400;font-size:22px;letter-spacing:1px}
.links{left:561px}
.links a{display:block;color:#fff;text-decoration:none;font-size:13px;margin-top:18px}
.links h3+a{margin-top:16px}
.contact{left:870px;width:230px}
.contact .row{display:flex;gap:16px;font-size:12.5px;line-height:19px;margin-top:14px;align-items:flex-start}
.contact .row i{flex:none;width:22px;height:22px;border-radius:50%;background:#fff;display:flex;align-items:center;justify-content:center}
.footer-rule{position:absolute;left:113px;top:290px;width:974px;height:1px;background:#555}
.copyright{position:absolute;top:314px;width:100%;text-align:center;font-size:12px}
</style>
</head>
<body>

<div class="topbar">Currently I am available between 9am to 5pm on Wednesdays only.</div>

<header class="site-header">
  <div class="brand"><span class="brand-mark"></span><span class="brand-name">Kestrelford</span></div>
  <nav class="nav"><span>Home</span><span>About Me</span><span>Services</span><span>Contact us</span></nav>
  <span class="btn">BOOK AN APPOINTMENT</span>
</header>

<section class="hero">
  <div class="photo" role="img" aria-label="Therapist taking notes on a clipboard while speaking with a client in a bright office"></div>
  <div class="hero-text">
    <div class="pre">WELCOME TO</div>
    <h1>KESTRELFORD</h1>
    <div class="sub">Therapy and Consulting</div>
  </div>
  <span class="btn">GET STARTED</span>
  <svg class="curve" width="1200" height="140" viewBox="0 0 1200 140">
    <path d="M0 0 Q600 210 1200 0 L1200 140 L0 140 Z" fill="#fff"/>
    <path d="M0 0 Q600 210 1200 0" fill="none" stroke="#c485da" stroke-width="9"/>
  </svg>
  <div class="dots"><i></i><i class="on"></i><i></i></div>
</section>

<section class="about">
  <div class="photo" role="img" aria-label="Portrait of the psychologist against green foliage"></div>
  <div class="about-body">
    <h2 class="heading">ABOUT ME</h2>
    <div class="name">Mr Daniel Ashworth</div>
    <div class="role">Kestrelford Therapy and Consulting</div>
    <p>I'm a clinical psychologist, psychotherapist, EMDR Consultant, and Resource Therapy Practitioner and Trainer. My main interest in therapy is helping people overcome the inner obstacles that cause them emotional pain and suffering, and that maintain behavioural patterns that are damaging or self-defeating. I also like to train, coach and mentor other therapists in effective therapies.</p>
    <div class="qual-h">QUALIFICATIONS</div>
    <div class="qual">BAppSc(Hons), MPsych(Clin)</div>
  </div>
  <span class="btn">LEARN MORE</span>
</section>

<section class="services">
  <h2 class="heading">OUR SERVICES</h2>
  <div class="cards">
    <div class="card raised">
      <svg width="64" height="64" viewBox="0 0 64 64" fill="none" stroke="#333" stroke-width="2"><circle cx="16" cy="18" r="6"/><path d="M8 54V32h16v22M16 32v22"/><circle cx="40" cy="40" r="4"/><circle cx="54" cy="40" r="4"/><path d="M34 54c0-6 12-6 12 0M48 54c0-6 12-6 12 0"/><rect x="34" y="6" width="24" height="16" rx="8"/></svg>
      <span>Psychotherapy</span>
    </div>
    <div class="card">
      <svg width="64" height="64" viewBox="0 0 64 64" fill="none" stroke="#333" stroke-width="2"><rect x="12" y="6" width="36" height="50"/><path d="M18 14h24M18 20h24"/><circle cx="32" cy="36" r="10"/><path d="M27 36l4 4 7-7M40 44l12 12"/></svg>
      <span>Assessment</span>
    </div>
    <div class="card raised">
      <svg width="64" height="64" viewBox="0 0 64 64" fill="none" stroke="#333" stroke-width="2"><circle cx="32" cy="34" r="14"/><circle cx="32" cy="31" r="5"/><path d="M24 44c2-6 14-6 16 0M10 24V10M10 10l-5 5M10 10l5 5M54 24V10M54 10l-5 5M54 10l5 5M32 8V2"/></svg>
      <span>Professional Training</span>
    </div>
    <div class="card">
      <svg width="64" height="64" viewBox="0 0 64 64" fill="none" stroke="#333" stroke-width="2"><rect x="6" y="10" width="52" height="36"/><path d="M27 20l12 8-12 8z"/><path d="M6 54h52"/><circle cx="20" cy="54" r="2" fill="#333"/></svg>
      <span>Online Video</span>
    </div>
  </div>
  <span class="btn">VIEW ALL</span>
</section>

<section class="interests">
  <h2 class="heading">AREAS OF SPECIAL INTEREST</h2>
  <span class="arrow" style="left:68px"><svg width="27" height="27" viewBox="0 0 27 27"><path d="M15 8l-5 5.5 5 5.5" fill="none" stroke="#33c3df" stroke-width="1.5"/></svg></span>
  <span class="arrow" style="left:1101px"><svg width="27" height="27" viewBox="0 0 27 27"><path d="M12 8l5 5.5-5 5.5" fill="none" stroke="#999" stroke-width="1.5"/></svg></span>
  <div class="topic" style="left:97px"><div class="photo" role="img" aria-label="Person looking distressed in a support group" style="background:linear-gradient(135deg,#8f8a84,#4e4a46)"></div><span>ADDICTION</span></div>
  <div class="topic" style="left:298px"><div class="photo" role="img" aria-label="Man looking frustrated in low light" style="background:linear-gradient(135deg,#6b5a49,#2a2420)"></div><span>ANGER RELATED<br>ISSUES</span></div>
  <div class="topic" style="left:499px"><div class="photo" role="img" aria-label="Person standing still in a blurred crowd" style="background:linear-gradient(135deg,#c9c7c4,#5a5754)"></div><span>ANXIETY</span></div>
  <div class="topic" style="left:700px"><div class="photo" role="img" aria-label="Person sitting hunched in a dark room" style="background:linear-gradient(135deg,#6a6a6a,#1c1c1c)"></div><span>DEPRESSION</span></div>
  <div class="topic" style="left:901px"><div class="photo" role="img" aria-label="Older couple sitting apart after a disagreement" style="background:linear-gradient(135deg,#c8d2d6,#8aa48a)"></div><span>RELATIONSHIP<br>ISSUES</span></div>
</section>

<section class="modalities">
  <div class="photo" role="img" aria-label="Father and teenage son sitting on a sofa during a counselling session"></div>
  <div class="mod-text">
    <h2 class="heading">MODALITIES</h2>
    <p>EMDR, Existential, Integrative, Mindfulness, Person Centred, Psychodynamic, Schema Therapy, CBT I believe that using Eye Movement Desensitizing and Reprocessing (EMDR) therapy and Resource Therapy (RT) together addresses almost all mental illness that doesn't involve an organic component. EMDR principally addresses disturbing memories from the past that negatively impact a person in the present. RT addresses resource states (also known as states of mind, parts, ego states, and schema modes) that are putting a person 'out of balance', i.e. they are yielding unwanted emotions or unwanted behaviours that are impairing a person's ability to function.</p>
  </div>
  <span class="outline-btn">LEARN MORE</span>
</section>

<section class="associations">
  <div class="assoc-frame"></div>
  <div class="photo" role="img" aria-label="Client and therapist sitting opposite each other in armchairs"></div>
  <div class="assoc-body">
    <h2 class="heading">PROFESSIONAL<br>ASSOCIATIONS</h2>
    <ul>
      <li><svg width="20" height="20" viewBox="0 0 20 20"><circle cx="10" cy="10" r="10" fill="#c485da"/><path d="M7 6l5 4-5 4" fill="none" stroke="#fff" stroke-width="2"/></svg>National Psychology Society</li>
      <li><svg width="20" height="20" viewBox="0 0 20 20"><circle cx="10" cy="10" r="10" fill="#c485da"/><path d="M7 6l5 4-5 4" fill="none" stroke="#fff" stroke-width="2"/></svg>EMDR Practitioners Association (Accredited Practitioner &amp; Consultant)</li>
      <li><svg width="20" height="20" viewBox="0 0 20 20"><circle cx="10" cy="10" r="10" fill="#c485da"/><path d="M7 6l5 4-5 4" fill="none" stroke="#fff" stroke-width="2"/></svg>Resource Therapy Institute (Clinical Resource Therapist &amp; Trainer</li>
    </ul>
  </div>
  <span class="btn">LEARN MORE</span>
</section>

<section class="info-tabs">
  <span class="tab active" style="left:227px;width:194px">QUALITY PROVISION</span>
  <span class="tab" style="left:436px;width:157px">BACKGROUND</span>
  <span class="tab" style="left:608px;width:243px">TRANSPORT AND PARKING</span>
  <span class="tab" style="left:864px;width:107px">FEES</span>
  <div class="tab-body">
    <h2 class="heading">QUALITY PROVISION</h2>
    <p>I generally start sessions checking with how clients are feeling and coping between sessions, ascertaining whether or not the client believes we are "on track" according to what was agreed in the treatment plan we co-created. I endeavour to maximise the benefit we can obtain from the number of sessions available to us.</p>
  </div>
  <span class="btn">LEARN MORE</span>
  <div class="photo" role="img" aria-label="Worried client with clasped hands while a therapist takes notes"></div>
</section>

<section class="payment">
  <h2 class="heading">PAYMENT OPTIONS</h2>
  <p>I currently accept EFT transfers only. I can process Medicare webclaims online on behalf of clients where they are registered with Medicare, i.e. Medicare already have their bank account details on file to be able to deposit the rebate into.</p>
</section>

<footer class="site-footer">
  <div class="brand"><span class="brand-mark"></span><span class="brand-name">Kestrelford</span></div>
  <div class="social" aria-label="Social media links"><i></i><i></i><i></i></div>
  <div class="f-col links">
    <h3>QUICK LINKS</h3>
    <a>Home</a><a>About Me</a><a>Services</a><a>Contact us</a>
  </div>
  <div class="f-col contact">
    <h3>CONTACT DETAILS</h3>
    <div class="row"><i><svg width="12" height="12" viewBox="0 0 12 12"><path d="M2 1l2 0 1 3-1.5 1a6 6 0 003.5 3.5L8 7l3 1v2a1 1 0 01-1 1A9 9 0 011 2a1 1 0 011-1z" fill="#111"/></svg></i><span>0400 000 123</span></div>
    <div class="row"><i><svg width="12" height="12" viewBox="0 0 12 12"><rect x="1" y="3" width="10" height="7" fill="none" stroke="#111" stroke-width="1.3"/><path d="M1 3l5 4 5-4" fill="none" stroke="#111" stroke-width="1.3"/></svg></i><span>info@kestrelford.com</span></div>
    <div class="row"><i><svg width="12" height="12" viewBox="0 0 12 12"><path d="M6 11S2 7 2 4.5a4 4 0 018 0C10 7 6 11 6 11z" fill="#111"/><circle cx="6" cy="4.5" r="1.4" fill="#fff"/></svg></i><span>Suite 4, Marlow House, 12 Harbour Street, Kestrelford, TAS 7000</span></div>
    <div class="row"><i><svg width="12" height="12" viewBox="0 0 12 12"><circle cx="6" cy="6" r="4.6" fill="none" stroke="#111" stroke-width="1.3"/><path d="M6 3.5V6l2 1" fill="none" stroke="#111" stroke-width="1.3"/></svg></i><span>Mon-8.00 to Fir-8.00</span></div>
  </div>
  <div class="footer-rule"></div>
  <div class="copyright">Copyright © 2024 Kestrelford . All rights reserved.</div>
</footer>

</body>
</html>
```